Super elegant, crisp & clean Business card design required

We recently upgraded our branding - which is on our website - talvendoraphoto.com

I would like a simple, yet elegant, clean business card design please.

The font of my logo is Cinzel - and because of the natural colour - it's best to have this on a black background.

I would like to have the back of the business card - with simply my logo.

PLEASE DO NOT SUBMIT A COMPLICATED / UNCLEAN DESIGN

Industry/Entity Type

Business

Contact Information for Business Card

Talven Doroshko Photography

Font styles to use
Other font styles liked:
• Cinzel

Requirements
Must have
• A backpage with nothing but my logo
• Simple design - stands out
Should not have
• Colour that dont align with my logo
• Over complicated '/ non symmetrical design

```html
<!DOCTYPE html>
<html lang="en">
<head>
<meta charset="utf-8">
<title>Talven Doroshko Photography – Business Card</title>
<link rel="stylesheet" href="https://fonts.googleapis.com/css2?family=Cinzel:wght@400;600&family=Lato:wght@400&display=swap">
<style>
  :root {
    --backdrop: #1d1d1f;
    --card-white: #ffffff;
    --card-shade: #eceae7;
    --taupe: #a89a80;
    --taupe-light: #bcae94;
    --taupe-dark: #8f8169;
    --brand: #8c7d63;
    --ink-light: #ffffff;
    --rule: rgba(255,255,255,0.85);
  }
  * { box-sizing: border-box; margin: 0; padding: 0; }
  html, body {
    width: 1200px; height: 922px; overflow: hidden;
    background: var(--backdrop);
  }
  .stage { position: relative; width: 1200px; height: 922px; }

  .card {
    position: absolute;
    width: 560px; height: 340px;
    border-radius: 18px;
    overflow: hidden;
    background: radial-gradient(ellipse at 50% 45%, var(--card-white) 55%, var(--card-shade) 100%);
  }
  .card--logo { left: 90px; top: 80px; }
  .card--contact { left: 550px; top: 500px; display: flex; }

  .wordmark {
    display: flex; flex-direction: column; align-items: center;
    font-family: "Cinzel", serif; font-weight: 400; color: var(--brand);
    text-align: center;
  }
  .wordmark__dot {
    width: 14px; height: 14px; border-radius: 50%;
    background: var(--brand); margin-bottom: 22px;
  }
  .wordmark__name { font-size: 30px; letter-spacing: 0.5px; line-height: 1.1; }
  .wordmark__line { font-size: 14px; letter-spacing: 9px; margin-top: 4px; padding-left: 9px; }

  .card--logo .wordmark {
    position: absolute; left: 0; right: 0; top: 118px;
  }

  .contact__brand {
    width: 47%; display: flex; align-items: center; justify-content: center;
  }
  .contact__brand .wordmark__name { font-size: 21px; }
  .contact__brand .wordmark__line { font-size: 10px; letter-spacing: 6px; padding-left: 6px; }
  .contact__brand .wordmark__dot { width: 10px; height: 10px; margin-bottom: 16px; }

  .contact__panel {
    width: 53%;
    background: linear-gradient(160deg, var(--taupe-dark) 0%, var(--taupe) 45%, var(--taupe-light) 100%);
    display: flex; flex-direction: column; justify-content: center;
    padding: 18px 22px 18px 0;
  }
  .contact__row {
    position: relative;
    display: flex; align-items: center;
    height: 72px;
    border-bottom: 1.5px solid var(--rule);
    margin-left: 38px;
    font-family: "Lato", sans-serif; font-size: 14px; letter-spacing: 1.6px;
    color: var(--ink-light);
  }
  .contact__row:last-child { border-bottom: none; }
  .contact__tab {
    position: absolute; left: -52px; top: 50%; transform: translateY(-50%);
    width: 40px; height: 34px; border-radius: 4px;
    background: var(--taupe-dark);
    display: flex; align-items: center; justify-content: center;
  }
  .contact__tab svg { width: 20px; height: 20px; }
  .contact__person { display: flex; flex-direction: column; font-family: "Cinzel", serif; }
  .contact__name { font-size: 17px; font-weight: 600; letter-spacing: 1.5px; }
  .contact__role { font-size: 11px; letter-spacing: 1.5px; margin-top: 2px; }
</style>
</head>
<body>
<main class="stage">

  <section class="card card--logo" aria-label="Card back with logo">
    <div class="wordmark">
      <span class="wordmark__dot"></span>
      <span class="wordmark__name">Talven Doroshko</span>
      <span class="wordmark__line">Photography</span>
    </div>
  </section>

  <section class="card card--contact" aria-label="Card front with contact details">
    <div class="contact__brand">
      <div class="wordmark">
        <span class="wordmark__dot"></span>
        <span class="wordmark__name">Talven Doroshko</span>
        <span class="wordmark__line">Photography</span>
      </div>
    </div>

    <div class="contact__panel">
      <div class="contact__row">
        <span class="contact__tab">
          <svg viewBox="0 0 20 20" fill="#fff"><circle cx="10" cy="6" r="4"/><path d="M2 19c0-5 3.5-7 8-7s8 2 8 7z"/></svg>
        </span>
        <div class="contact__person">
          <span class="contact__name">Talven Doroshko</span>
          <span class="contact__role">Owner</span>
        </div>
      </div>
      <div class="contact__row">
        <span class="contact__tab">
          <svg viewBox="0 0 20 20" fill="none" stroke="#fff" stroke-width="1.6"><rect x="5" y="1.5" width="10" height="17" rx="2"/><line x1="8.5" y1="15.5" x2="11.5" y2="15.5"/></svg>
        </span>
        <span>07700900418</span>
      </div>
      <div class="contact__row">
        <span class="contact__tab">
          <svg viewBox="0 0 20 20" fill="none" stroke="#fff" stroke-width="1.6"><circle cx="10" cy="10" r="8"/><ellipse cx="10" cy="10" rx="3.5" ry="8"/><line x1="2" y1="10" x2="18" y2="10"/></svg>
        </span>
        <span>www.talvendoraphoto.com</span>
      </div>
      <div class="contact__row">
        <span class="contact__tab">
          <svg viewBox="0 0 20 20" fill="none" stroke="#fff" stroke-width="1.6"><rect x="2" y="4" width="16" height="12" rx="1.5"/><path d="M2.5 5l7.5 6 7.5-6"/></svg>
        </span>
        <span>info@talvendoraphoto.com</span>
      </div>
    </div>
  </section>

</main>
</body>
</html>
```